Dew and Willow med spa needs an awesome eye catching billboard ad

We need a billboard ad design for a Med Spa with location sin Davenport and Windermere FL A medical spa where the beauty of nature meets the power of science to treat the whole person, mind, body and soul.

Marigold Radiance Med Spa is a medical spa where the beauty of nature meets the power of science to create gorgeous, youthful looking skin. Located in Davenport, Florida, but also serving Four Corners, Celebration, and Windermere, Florida, the talented professional team brings decades of experience in world-class skin care to provide holistic, science-backed aesthetic services and health coaching.

Industry/Entity Type

Spa

Colors
fbee3e
fece3e
eea4c8
e667a6
fbee3d

Requirements
Must have
• Locations in Davenport and Dr Phillips
Phone 407-555-0148
website www.dewandwillow-example.com

Boards for each:
Aesthetic Treatments
Cosmetic Injectables
Quoria facial
add color vs too many earthtones, to catch the eye perhaps using yellow, something that catches the eye and stands out from the normal everyday
Thank you!!!!
Nice to have
• Boards for each:
Aesthetic Treatments
Cosmetic Injectables
Quoria facial
add color vs too many earthtones, to catch the eye
photos that match services,
Thank you!!!!

```html
<!DOCTYPE html>
<html lang="en">
<head>
<meta charset="utf-8">
<title>Marigold Radiance Med Spa — Aesthetic Treatments Billboard</title>
<link rel="stylesheet" href="https://fonts.googleapis.com/css2?family=Cinzel:wght@400;600&family=Marcellus&display=swap">
<style>
  :root {
    --page-bg: #e9edf1;
    --board-bg: #f9f8f6;
    --brand-pink: #e667a6;
    --blush: #eea4c8;
    --sun: #fbee3e;
    --sun-deep: #fece3e;
    --ink: #4b4b4d;
    --photo-warm: #f0cfc0;
    --photo-hair: #8a6a58;
    --photo-light: #f6efe6;
  }
  * { margin: 0; padding: 0; box-sizing: border-box; }
  html, body {
    width: 1143px;
    height: 1200px;
    overflow: hidden;
    background: var(--page-bg);
  }
  .billboard {
    position: absolute;
    left: 0;
    top: 453px;
    width: 1143px;
    height: 293px;
    background: var(--board-bg);
    overflow: hidden;
  }
  .flower-decor {
    position: absolute;
    border-radius: 50%;
  }
  .flower-decor--top-left {
    left: -30px; top: -30px; width: 150px; height: 135px;
    background: radial-gradient(circle, var(--blush) 0%, rgba(238,164,200,0.55) 60%, rgba(238,164,200,0) 100%);
  }
  .flower-decor--top-right {
    left: 1000px; top: -20px; width: 170px; height: 185px;
    background: radial-gradient(circle, var(--sun) 0%, rgba(251,238,62,0.55) 60%, rgba(251,238,62,0) 100%);
  }
  .flower-decor--bottom-left {
    left: 8px; top: 238px; width: 80px; height: 60px;
    background: radial-gradient(circle, var(--blush) 0%, rgba(238,164,200,0.5) 60%, rgba(238,164,200,0) 100%);
  }

  .brand-mark {
    position: absolute;
    left: 250px;
    top: 46px;
    width: 46px;
    height: 46px;
    border-radius: 50%;
    background: var(--brand-pink);
  }
  .brand-name {
    position: absolute;
    left: 316px;
    top: 30px;
    font-family: "Cinzel", serif;
    font-weight: 400;
    color: var(--brand-pink);
    line-height: 1;
    white-space: nowrap;
  }
  .brand-name__main { display: block; font-size: 50px; letter-spacing: 10px; }
  .brand-name__sub { display: block; margin-top: 12px; margin-left: 16px; font-size: 20px; letter-spacing: 7px; }

  .locations {
    position: absolute;
    left: 334px;
    top: 140px;
    font-family: "Cinzel", serif;
    font-size: 14px;
    letter-spacing: 4px;
    color: var(--ink);
    white-space: nowrap;
  }
  .locations__dot { color: var(--brand-pink); margin: 0 8px; }

  .service-band {
    position: absolute;
    left: 0;
    top: 174px;
    width: 820px;
    height: 52px;
    background: linear-gradient(90deg, var(--sun-deep) 0%, var(--sun) 16%, rgba(251,238,62,0.45) 60%, rgba(251,238,62,0) 100%);
  }
  .service-title {
    position: absolute;
    left: 128px;
    top: 180px;
    font-family: "Cinzel", serif;
    font-weight: 600;
    font-size: 40px;
    letter-spacing: 3px;
    color: var(--ink);
    white-space: nowrap;
    line-height: 1;
  }
  .contact-line {
    position: absolute;
    left: 118px;
    top: 238px;
    display: flex;
    align-items: center;
    gap: 14px;
    color: var(--ink);
    white-space: nowrap;
  }
  .contact-line__web {
    font-family: "Cinzel", serif;
    font-size: 17px;
    letter-spacing: 0.2px;
  }
  .contact-line__divider {
    width: 2px;
    height: 38px;
    background: var(--ink);
  }
  .contact-line__phone {
    font-family: "Marcellus", serif;
    font-size: 42px;
    line-height: 1;
  }
  .hero-photo {
    position: absolute;
    left: 790px;
    top: 0;
    width: 353px;
    height: 293px;
    background:
      radial-gradient(ellipse 45% 70% at 48% 55%, rgba(138,106,88,0.55) 0%, rgba(138,106,88,0) 100%),
      linear-gradient(180deg, rgba(249,248,246,0) 0%, var(--photo-light) 40%, #eeb0b8 100%);
  }
</style>
</head>
<body>
  <main class="billboard">
    <div class="flower-decor flower-decor--top-left" role="img" aria-label="Soft flower decoration"></div>
    <div class="flower-decor flower-decor--top-right" role="img" aria-label="Soft flower decoration"></div>
    <div class="flower-decor flower-decor--bottom-left" role="img" aria-label="Soft flower decoration"></div>

    <div class="brand-mark"></div>
    <h1 class="brand-name">
      <span class="brand-name__main">MARIGOLD</span>
      <span class="brand-name__sub">RADIANCE MED SPA</span>
    </h1>
    <p class="locations">DAVENPORT<span class="locations__dot">•</span>DR PHILLIPS</p>

    <div class="service-band"></div>
    <h2 class="service-title">AESTHETIC TREATMENTS</h2>

    <p class="contact-line">
      <span class="contact-line__web">WWW.DEWANDWILLOW-EXAMPLE.COM</span>
      <span class="contact-line__divider"></span>
      <span class="contact-line__phone">407-555-0148</span>
    </p>

    <div class="hero-photo" role="img" aria-label="Photo of a relaxed woman in a straw hat and pink top, sunlit waterfront behind her"></div>
  </main>
</body>
</html>
```